Orthobiologic, StemCell, Bone Marrow Aspirate Device Distributor

We need a wordpress fully functioning website design for an innovative ortho-biologic, Bone Marrow Aspirate Device that extracts stem cells for orthopedic regenerative medical professionals. We also offer state of the art training in there office setting with licensed medical staff, a full service support team, and software for tracking patient outcome over time. We are an innovative company that prides itself on gold standard support. We will have other offerings on our website and would like a spot for "future" products. We would like to see designs that look professional, medical, and convey support, security, science, and innovation. We prefer shades of blue and red/orange. I particularly like the following websites that also sell the same device in order of preference:regenacelltherapy.comhttps://aspire-medical.eu/marrow-cellution/https://www.matrixbiosurgical.com/#emerging-solutions-in-healthcareElite2elite.comI have attached a few pictures of the device for reference

Target Market(s)

Orthopedics, Regenerative medicine doctors, Industry representatives, Hospitals

Industry/Entity Type

Medical Equipment

Coding

Coded - Design and coding required

Colors
3176b5
33a6d7
f37022
ec1f27

Requirements
Must have
• It must be able to have videos which I can supply, email, online ordering, and sfax. I have a domain name Coralweavesolutions.com . It must have a FAQ section which you can obtain some information from https://www.tolvenclinical.com/solutions#resources
• The device is manufactured by Dulmor and this is the link to the product page http://www.dulmor.com/quintadraw
• I am currently working on a custom logo and should be able to supply that in short order. I prefer shades of blue and red.
Nice to have
• I would love to have a graphic video as seen here: please see quinta draw vs bone marrow aspirate concentrate.
• https://www.tolvenclinical.com/solutions#competition
• I would pay considerably more to have something similar if it is at all possible
Should not have
• Nothing specific

```html
<!DOCTYPE html>
<html lang="en">
<head>
<meta charset="utf-8">
<title>Coralweave Solutions</title>
<link href="https://fonts.googleapis.com/css2?family=Open+Sans:wght@400;600;700&display=swap" rel="stylesheet">
<style>
:root{
  --orange:#f37022;
  --red:#ec1f27;
  --navy:#0d1f4f;
  --blue:#3176b5;
  --sky:#33a6d7;
  --ink:#222;
  --grey-bg:#eeeff1;
  --card-grey:#e2e2e2;
  --footer:#050505;
}
*{box-sizing:border-box;margin:0;padding:0}
html,body{width:1200px;height:4222px;overflow:hidden}
body{font-family:"Open Sans",Arial,sans-serif;color:var(--ink);background:#fff;position:relative}
section,header,footer{position:relative;width:1200px;overflow:hidden}
.abs{position:absolute}

/* header */
.site-header{height:152px;background:#f6f6f6}
.brand{left:98px;top:7px;width:143px;height:132px;background:var(--orange);color:#fff;text-align:center;font-weight:700;padding-top:38px}
.brand-name{font-size:19px;line-height:24px}
.brand-sub{font-size:13px;line-height:22px}
.call{left:760px;top:28px;display:flex;align-items:center;gap:10px}
.call-label{font-size:14px;font-weight:600;color:var(--blue);line-height:16px}
.call-number{font-size:16px;font-weight:700;color:var(--blue)}
.search{left:939px;top:41px;width:160px;height:28px;border:2px solid var(--orange);border-radius:14px;font-size:13px;color:#555;padding:4px 14px;display:flex;justify-content:space-between;align-items:center}
.main-nav{right:100px;top:110px;display:flex;gap:24px;font-size:14px;font-weight:700;color:#111}

/* hero */
.hero{height:725px}
.hero-art{left:0;top:0;width:1200px;height:725px;background:radial-gradient(circle at 22% 55%,#f0a868 0%,#7d6478 22%,#2c4a74 48%,#1d3554 75%,#152640 100%)}
.hero-panel{left:279px;top:199px;width:660px;height:285px;background:rgba(40,52,80,.72);text-align:center;color:#fff}
.hero-title{font-size:52px;font-weight:600;margin-top:44px;line-height:60px;display:inline-block;border-bottom:5px solid var(--orange);padding:0 2px}
.hero-sub{font-size:17px;line-height:28px;margin-top:6px}
.btn{display:inline-block;background:var(--red);color:#fff;font-weight:600}
.hero-btn{width:216px;height:34px;line-height:34px;font-size:16px;margin-top:14px}
.dots{display:flex;gap:8px}
.dot{width:20px;height:20px;border-radius:50%;background:#fff}
.hero-dots{left:568px;top:594px}
.hero-wave{left:0;bottom:0}

/* welcome */
.welcome{height:513px}
.welcome-text{left:98px;top:95px;width:518px}
.welcome h2{font-weight:400;font-size:30px;line-height:36px;color:#111}
.welcome h2 strong{display:block;font-weight:700;color:var(--navy)}
.welcome p{font-size:15px;line-height:36px;text-align:justify;margin-top:12px}
.read-more{margin-top:22px;width:155px;height:34px;line-height:34px;text-align:center;font-size:14px;font-weight:700}
.welcome-frame{left:662px;top:100px;width:390px;height:293px;border:3px solid var(--red)}
.welcome-photo{left:713px;top:118px;width:385px;height:292px;background:linear-gradient(135deg,#a9d8d8,#5fb6b2 55%,#e6f1ef)}

/* products */
.products{height:659px;background:var(--orange)}
.section-title{width:1200px;text-align:center;font-size:31px;font-weight:700}
.products .section-title{top:24px;color:#fff}
.products .section-title span{color:var(--navy)}
.product-card{top:110px;width:320px;height:459px;background:var(--navy);color:#fff;box-shadow:0 2px 6px rgba(0,0,0,.3)}
.product-photo{height:254px;position:relative}
.product-badge{position:absolute;left:136px;top:228px;width:50px;height:50px;border-radius:50%;border:2px solid #fff;background:var(--navy)}
.product-body{padding:20px 18px 0}
.product-body h3{font-size:16px;font-weight:700}
.product-body p{font-size:16px;line-height:28px;margin-top:12px;text-align:justify}
.product-btn{margin-top:8px;font-size:14px;padding:0 12px;height:26px;line-height:26px;font-weight:700}
.products-dots{left:568px;top:612px}
.products-dots .dot{background:#fff}
.products-dots .dot.active{background:var(--navy)}

/* team */
.team{height:664px}
.team .section-title{top:90px;color:#111}
.team .section-title span{color:var(--orange)}
.member{top:156px;width:321px;height:402px;background:var(--card-grey);border-bottom:4px solid var(--red);text-align:center}
.member-photo{height:302px}
.member-name{font-size:15px;font-weight:700;color:var(--navy);margin-top:20px}
.socials{display:flex;justify-content:center;gap:7px;margin-top:10px}
.socials span{width:24px;height:24px;border-radius:50%;background:var(--navy)}

/* comparison */
.compare{height:557px;background:linear-gradient(120deg,#0d2734,#1b4454 50%,#0f2a38)}
.compare .section-title{top:32px;color:#fff;font-size:23px}
.compare .section-title span{color:var(--orange);font-size:18px;margin:0 12px}
.video{top:107px;width:434px;height:279px;background:radial-gradient(ellipse at 50% 45%,#a4222e,#c85a6a 45%,#d87e8a 100%)}
.play{position:absolute;left:197px;top:119px}
.points{top:400px;width:434px;list-style:none;color:#fff;font-size:15px}
.points li{line-height:35px;padding-left:16px;position:relative}
.points li::before{content:"";position:absolute;left:3px;top:16px;width:5px;height:5px;border-radius:50%;background:var(--orange)}

/* faq */
.faq{height:582px;background:var(--grey-bg)}
.faq .section-title{top:28px;color:var(--orange)}
.faq-list{left:98px;top:108px;width:1004px}
.faq-item{display:flex;gap:18px;padding:0 0 18px 20px;border-bottom:1px solid #555;margin-bottom:24px}
.faq-icon{flex:0 0 32px;height:32px;border:2px solid var(--orange);border-radius:50%;color:var(--orange);font-weight:700;font-size:24px;line-height:26px;text-align:center;margin-top:2px}
.faq-q{font-size:22px;font-weight:700;color:#111;line-height:26px}
.faq-a{padding:8px 0 0 94px;font-size:22px;font-weight:700;line-height:26px;color:#111;width:960px}
.faq-wave{left:0;bottom:0}

/* footer */
.site-footer{height:370px;background:var(--footer);color:#fff}
.footer-col h4{font-size:19px;font-weight:700}
.about-col{left:167px;top:52px;width:284px}
.about-col p{font-size:14px;line-height:21px;margin-top:16px;text-align:justify}
.ring-row{display:flex;gap:10px;margin-top:14px}
.ring-row span{width:36px;height:36px;border:2px solid #fff;border-radius:50%}
.links-col{left:520px;top:52px}
.links-col ul{list-style:none;margin-top:16px;font-size:14px;line-height:26px}
.contact-col{left:733px;top:50px;width:320px}
.field{background:#fff;color:#333;font-size:13px;height:36px;padding:8px 14px;margin-top:8px;border:1px solid #ccc}
.field.message{height:70px}
.submit{margin-top:10px;width:124px;height:32px;line-height:32px;text-align:center;font-size:14px;font-weight:700}
.footer-rule{left:98px;top:312px;width:1004px;height:1px;background:#888}
.copyright{top:330px;width:1200px;text-align:center;font-size:14px}
</style>
</head>
<body>

<header class="site-header">
  <div class="brand abs"><div class="brand-name">CORALWEAVE</div><div class="brand-sub">SOLUTIONS</div></div>
  <div class="call abs">
    <svg width="30" height="30" viewBox="0 0 30 30"><circle cx="15" cy="15" r="13" fill="none" stroke="#f37022" stroke-width="1.5"/><path d="M10 9c1-1 2-1 3 0l1 2c0 1-1 1-1 2 1 2 2 3 4 4 1 0 1-1 2-1l2 1c1 1 1 2 0 3-2 2-6 0-8-2s-5-6-3-9z" fill="none" stroke="#3176b5" stroke-width="1.4"/></svg>
    <div><div class="call-label">CALL US</div><div class="call-number">888-555-0142</div></div>
  </div>
  <div class="search abs"><span>Search</span>
    <svg width="13" height="13" viewBox="0 0 13 13"><circle cx="5.5" cy="5.5" r="4" fill="none" stroke="#222" stroke-width="1.6"/><path d="M8.5 8.5l3.5 3.5" stroke="#222" stroke-width="1.6"/></svg>
  </div>
  <nav class="main-nav abs"><span>ABOUT</span><span>PRODUCTS</span><span>PROVIDERS</span><span>TEAM</span><span>FAQ'S</span><span>CONTACT</span></nav>
</header>

<section class="hero">
  <div class="hero-art abs" role="img" aria-label="Glowing DNA double helix strands on a deep blue background"></div>
  <div class="hero-panel abs">
    <h1 class="hero-title">STEM CELL THERAPY</h1>
    <p class="hero-sub">IMPLEMENTING BONE MARROW DERIVED STEM CELLS<br>IN YOUR PRACTICE</p>
    <span class="btn hero-btn">VIEW DETAILS</span>
  </div>
  <div class="dots hero-dots abs"><span class="dot"></span><span class="dot" style="background:var(--orange)"></span><span class="dot"></span></div>
  <svg class="hero-wave abs" width="1200" height="110" viewBox="0 0 1200 110" preserveAspectRatio="none">
    <path d="M0 40 C250 -10 450 20 700 70 C900 105 1080 80 1200 40 L1200 110 L0 110Z" fill="#33a6d7"/>
    <path d="M0 50 C250 5 450 30 700 78 C900 110 1080 88 1200 52 L1200 110 L0 110Z" fill="#f37022"/>
    <path d="M0 58 C250 15 450 40 700 88 C900 120 1080 100 1200 70 L1200 110 L0 110Z" fill="#3176b5"/>
    <path d="M0 70 C250 30 450 55 700 100 C900 130 1080 115 1200 88 L1200 110 L0 110Z" fill="#fff"/>
  </svg>
</section>

<section class="welcome">
  <div class="welcome-text abs">
    <h2>WELCOME TO <strong>CORALWEAVE SOLUTIONS</strong></h2>
    <p>Lorem Ipsum is simply dummy text of the printing and typesetting industry. Lorem Ipsum has been the industry's standard dummy text ever since the 1500s, when an unknown printer took a galley of type and scrambled it to make a type specimen book. It has survived not only five centuries</p>
    <div class="btn read-more">READ MORE</div>
  </div>
  <div class="welcome-frame abs"></div>
  <div class="welcome-photo abs" role="img" aria-label="Pipette filling teal sample wells in a laboratory tray"></div>
</section>

<section class="products">
  <h2 class="section-title abs">FEATURE <span>PRODUCTS</span></h2>
  <article class="product-card abs" style="left:97px">
    <div class="product-photo" style="background:linear-gradient(#000,#0a0a14)" role="img" aria-label="Blue-handled bone marrow aspiration needles on black"><span class="product-badge"></span></div>
    <div class="product-body"><h3>Quinta Draw</h3><p>Traditional method is to aspirate from the distal which collects a high level ofperipheral blood requiring</p><span class="btn product-btn">READ MORE</span></div>
  </article>
  <article class="product-card abs" style="left:439px">
    <div class="product-photo" style="background:linear-gradient(90deg,#f3e8e4,#f6b48a 50%,#f7f0ee)" role="img" aria-label="Platelet-rich plasma kit with syringe"><span class="product-badge"></span></div>
    <div class="product-body"><h3>Trivona PRP</h3><p>Traditional method is to aspirate from the distal which collects a high level ofperipheral blood requiring</p><span class="btn product-btn">READ MORE</span></div>
  </article>
  <article class="product-card abs" style="left:784px">
    <div class="product-photo" style="background:linear-gradient(90deg,#eee,#b9aa98 50%,#eee)" role="img" aria-label="Cell processing console with display screen"><span class="product-badge"></span></div>
    <div class="product-body"><h3>Quinta Draw</h3><p>Traditional method is to aspirate from the distal which collects a high level ofperipheral blood requiring</p><span class="btn product-btn">READ MORE</span></div>
  </article>
  <div class="dots products-dots abs"><span class="dot" style="width:17px;height:17px"></span><span class="dot active" style="width:17px;height:17px"></span><span class="dot" style="width:17px;height:17px"></span></div>
</section>

<section class="team">
  <h2 class="section-title abs">OUR <span>TEAM</span></h2>
  <article class="member abs" style="left:98px">
    <div class="member-photo" style="background:linear-gradient(135deg,#f4f4f4,#cfd6dc)" role="img" aria-label="Portrait of a smiling doctor in a white coat"></div>
    <div class="member-name">MARCUS HALE</div>
    <div class="socials"><span></span><span></span><span></span><span></span></div>
  </article>
  <article class="member abs" style="left:439px">
    <div class="member-photo" style="background:linear-gradient(135deg,#dfe6ee,#b8c6d4)" role="img" aria-label="Doctor greeting an elderly patient"></div>
    <div class="member-name">DEVIN ORR</div>
    <div class="socials"><span></span><span></span><span></span><span></span></div>
  </article>
  <article class="member abs" style="left:779px">
    <div class="member-photo" style="background:linear-gradient(135deg,#c9dbe8,#eef2f5)" role="img" aria-label="Portrait of a smiling female doctor with stethoscope"></div>
    <div class="member-name">LENA VOSS</div>
    <div class="socials"><span></span><span></span><span></span><span></span></div>
  </article>
</section>

<section class="compare">
  <h2 class="section-title abs">TRADITIONAL NEEDLES<span>VS</span>QUINTA DRAW</h2>
  <div class="video abs" style="left:100px" role="img" aria-label="Animation of a traditional needle aspirating marrow tissue">
    <svg class="play" width="40" height="40" viewBox="0 0 40 40"><circle cx="20" cy="20" r="18" fill="none" stroke="#fff" stroke-width="3"/><path d="M16 12l12 8-12 8z" fill="#fff"/></svg>
  </div>
  <div class="video abs" style="left:664px" role="img" aria-label="Animation of a closed-tip cannula aspirating marrow tissue">
    <svg class="play" width="40" height="40" viewBox="0 0 40 40"><circle cx="20" cy="20" r="18" fill="none" stroke="#fff" stroke-width="3"/><path d="M16 12l12 8-12 8z" fill="#fff"/></svg>
  </div>
  <ul class="points abs" style="left:110px">
    <li>Traditional bone marrow aspiration needles aspirate</li>
    <li>which leads to excess peripheral blood dilution</li>
    <li>Tarvik needles were designed to draw very small</li>
  </ul>
  <ul class="points abs" style="left:674px">
    <li>The closed-tip aspiration cannula restricts aspiration</li>
    <li>Avoiding excess peripheral blood infiltration.</li>
    <li>A mechanical means for measured and controlled</li>
  </ul>
</section>

<section class="faq">
  <h2 class="section-title abs">FAQ'S</h2>
  <div class="faq-list abs">
    <div class="faq-item"><span class="faq-icon">+</span><p class="faq-q">DOES A SMALL VOLUME ASPIRATE HAVE MORE CFU-F THAN A LARGER DRAW<br>THAT IS THEN VOLUME REDUCED BY CENTRIFUGATION?</p></div>
    <div class="faq-item"><span class="faq-icon">+</span><p class="faq-q">WHAT ARE THE LIMITATIONS OF TRADITIONAL NEEDLES AND WHAT IS THE OPTIMAL<br>TECHNIQUE FOR MINIMIZAING PERIPHERAL BLOOD DILUTION?</p></div>
    <div class="faq-item" style="margin-bottom:0;padding-top:8px"><span class="faq-icon">-</span><p class="faq-q">WHAT IS THE IMPORTANCE OF CFU-F COUNTS COMPARED TO NUCLEATED CELL<br>COUNTS?</p></div>
    <p class="faq-a" style="padding-top:24px">There is no constant ratio between average marrow cellularity as measured by<br>number of total nucleated cells per mL and the number of cfu-f.</p>
  </div>
  <svg class="faq-wave abs" width="1200" height="60" viewBox="0 0 1200 60" preserveAspectRatio="none">
    <path d="M0 30 C300 0 600 50 900 25 C1020 15 1120 10 1200 20 L1200 60 L0 60Z" fill="#33a6d7"/>
    <path d="M0 38 C300 8 600 58 900 33 C1020 23 1120 18 1200 28 L1200 60 L0 60Z" fill="#f37022"/>
    <path d="M0 46 C300 18 600 64 900 42 C1020 33 1120 28 1200 36 L1200 60 L0 60Z" fill="#050505"/>
  </svg>
</section>

<footer class="site-footer">
  <div class="footer-col about-col abs">
    <h4>ABOUT</h4>
    <p>Lorem Ipsum is simply dummy text of the printing and typesetting industry. Lorem Ipsum has been the industry's standard dummy text ever since the 1500s,</p>
    <div class="ring-row"><span></span><span></span><span></span><span></span></div>
  </div>
  <div class="footer-col links-col abs">
    <h4>QUICK LINKLS</h4>
    <ul><li>ABOUT</li><li>PRODUCTS</li><li>PROVIDERS</li><li>TEAM</li><li>FAQ'S</li><li>CONTACT</li></ul>
  </div>
  <div class="footer-col contact-col abs">
    <h4>CONTACT</h4>
    <div class="field" style="margin-top:16px">Name</div>
    <div class="field">Enter Your Email</div>
    <div class="field message">Message</div>
    <div class="btn submit">SUBMIT</div>
  </div>
  <div class="footer-rule abs"></div>
  <p class="copyright abs">copyrigts © 2019 All Rights Resrverd</p>
</footer>

</body>
</html>
```